Smack you in the face - Landing page for Residential Electrical Repairs (Searchly Ads)

I need an effective landing page for Searchly ads. The ads will target residential electrical repairs. Lighting Outages, Power Outages, Breakers Tripping, Outlets Not Working. I need a strong call to action to Call Us Now! Forms don't work well for us so we only need one form as a last option at the bottom of the page. We only work on homes. the website is https://www.vantor-wiring.example/
email is : support@vantor-wiring.example
Phone 555-217-4086

**This is about one focused service. Electrical Repairs - That includes Partial Power Outages, Outlets Not Working, Tripped Breakers, Electrical Panel repairs, and Fusebox Repairs. The area served will only be Greenville, SC. KOBA is the platform

Target Market(s)

Homeonwers in need of electrical repair

Industry/Entity Type

Residential Electricians

Coding

Coded - Design and coding required

Requirements
Must have
• Strong to action for phone calls, this landing page must grab action fast.
Nice to have
• Social proof with existing 5 start reviews for Searchly, Rately, TCB, and Friendnet
Should not have
• Should not be form based. I do not like the site's current them, please don't copy it. Make your own.

```html
<!DOCTYPE html>
<html lang="en">
<head>
<meta charset="utf-8">
<title>Vantor Wiring Service – Residential Electrical Repairs in Greenville, SC</title>
<link rel="stylesheet" href="https://fonts.googleapis.com/css2?family=Syncopate:wght@700&family=Montserrat:wght@400;500;600;700&display=swap">
<style>
:root{
  --orange:#f26a24;
  --teal:#1c6781;
  --teal-deep:#16566d;
  --ink:#17171f;
  --text:#3a3a44;
  --muted:#6b6b75;
  --paper:#ffffff;
  --field:#f4e3da;
}
*{box-sizing:border-box;margin:0;padding:0}
html,body{width:1200px;height:5314px;overflow:hidden}
body{position:relative;font-family:"Montserrat",sans-serif;color:var(--text);background:var(--paper)}
.abs{position:absolute}
.display{font-family:"Syncopate",sans-serif;font-weight:700;letter-spacing:1px;color:var(--ink);text-transform:uppercase}
.eyebrow{font-size:12px;text-transform:uppercase;letter-spacing:.3px}
.center{left:0;width:1200px;text-align:center}
.rule{width:44px;height:3px;background:var(--orange);margin:0 auto}

/* call button */
.cta{position:absolute;height:40px;display:flex;align-items:center;justify-content:center;background:var(--orange);color:var(--ink);font-size:12px;font-weight:600;text-transform:uppercase;letter-spacing:.2px}
.cta.light{background:#fff;color:var(--orange)}
.cta svg{position:absolute;left:-10px;top:-6px;width:30px;height:52px}

/* header / hero */
.hero{position:absolute;left:0;top:0;width:1200px;height:640px;background:linear-gradient(100deg,#f4f4f2 0%,#ebecea 50%,#dcdedc 100%);overflow:hidden}
.hero-photo{position:absolute;left:600px;top:0;width:600px;height:560px;background:linear-gradient(180deg,#cfd3d3 0%,#9fb3c6 45%,#5d86b5 100%);opacity:.75}
.topbar-mail{position:absolute;left:570px;top:0;width:322px;height:38px;background:#1c1c24;color:#fff;font-size:11px;display:flex;align-items:center;padding-left:60px;gap:10px;border-radius:0 0 0 0}
.topbar-call{position:absolute;left:890px;top:0;width:310px;height:38px;background:var(--orange);color:#fff;font-size:11px;line-height:13px;padding:3px 0 0 80px}
.brand{position:absolute;left:140px;top:20px;width:180px;text-align:center}
.brand .name{font-family:"Syncopate",sans-serif;font-weight:700;font-size:24px;color:var(--ink);letter-spacing:1px}
.brand .tag{font-size:9px;font-weight:600;color:var(--teal);letter-spacing:2.4px;text-transform:uppercase}
.hero h1{position:absolute;left:142px;top:140px;font-size:31px;line-height:40px}
.hero h1 .accent{color:var(--orange)}
.hero .lede{position:absolute;left:142px;top:270px;font-size:19px;line-height:28px;color:var(--ink);width:520px}
.hero-curves{position:absolute;left:0;top:0}

/* about */
.about-photo{left:140px;top:735px;width:440px;height:471px;background:radial-gradient(circle at 62% 40%,#c7ccd3 0%,#d9dde0 40%,#eef0f1 70%,#fff 100%)}
.about-copy{left:630px;top:780px;width:432px}
.about-copy h2{font-size:31px;margin:10px 0 28px}
.about-copy p{font-size:11px;line-height:18.5px;margin-bottom:10px;color:var(--text)}

/* services */
.services{left:0;top:1206px;width:1200px;height:788px;background:var(--teal)}
.services .eyebrow,.services h2{color:#fff}
.card{position:absolute;top:185px;width:216px;height:445px;background:#fff;border-radius:6px;padding:5px;text-align:center}
.card .shot{height:250px;border-radius:5px 5px 0 0}
.card h3{font-size:13px;font-weight:700;color:var(--ink);margin:38px 0 8px;text-transform:uppercase}
.card p{font-size:10.5px;line-height:18px;color:var(--text);padding:0 12px;height:80px}
.card a{font-size:10.5px;color:var(--orange);text-decoration:underline;font-weight:500}

/* try */
.try h2{color:var(--teal);font-size:30px;line-height:42px}

/* reviews */
.reviews{left:0;top:2336px;width:1200px;height:561px;background:var(--orange)}
.reviews .eyebrow,.reviews h2{color:var(--ink)}
.listings{position:absolute;top:185px;left:0;width:1200px;display:flex;justify-content:center;align-items:center;gap:34px;color:#fff;font-weight:700;font-size:16px}
.listings .stars{display:block;font-size:9px;letter-spacing:1px;text-align:center}
.listings .badge{width:74px;height:34px;background:#fff;border-radius:3px;opacity:.9}
.review{position:absolute;top:280px;width:442px;height:190px;background:#fff;text-align:center;padding:45px 14px 0}
.review h4{font-size:14px;font-weight:600;color:var(--ink)}
.review .stars{color:var(--orange);font-size:11px;letter-spacing:2px;margin:4px 0 12px}
.review p{font-size:10.5px;line-height:18px;color:var(--text)}
.avatar{position:absolute;top:245px;width:70px;height:70px;border-radius:50%;border:3px solid #fff;background:linear-gradient(160deg,#d2b4a0,#8a6a58)}
.review .src{position:absolute;right:14px;top:12px;width:26px;height:26px;border-radius:50%;background:#eee}
.nav-prev{position:absolute;left:84px;top:2694px;width:34px;height:34px;border-radius:50%;border:1px solid #fff;color:#fff;display:flex;align-items:center;justify-content:center;font-size:16px}
.nav-next{position:absolute;left:1090px;top:2696px;color:var(--ink);font-size:18px}

/* gallery */
.tile{position:absolute;border-radius:4px}
.tile.feature::after{content:"";position:absolute;inset:0;background:rgba(20,20,28,.55);border-radius:4px}
.tile .cap{position:absolute;z-index:1;left:20px;right:20px;top:135px;text-align:center;color:#fff}
.tile .cap h5{font-size:14px;font-weight:600;margin-bottom:8px}
.tile .cap p{font-size:10.5px;line-height:18px}
.tile .cap .plus{width:32px;height:32px;border:1px solid #fff;border-radius:50%;margin:10px auto 0;line-height:30px;font-size:20px}

/* need */
.need{left:0;top:3676px;width:1200px;height:277px;background:var(--teal)}
.need-person{left:168px;top:3552px;width:262px;height:401px;background:linear-gradient(180deg,#f0a35c 0%,#e05c48 35%,#2f5aa8 70%,#274a87 100%);border-radius:120px 120px 0 0}
.need h2{position:absolute;left:510px;top:70px;color:#fff;font-size:32px}
.need p{position:absolute;left:494px;top:122px;color:#fff;font-size:15.5px}

/* why */
.why .lead{font-size:12px;line-height:26px;color:var(--ink)}
.benefit{position:absolute;top:4200px;width:250px;text-align:center}
.benefit svg{width:70px;height:70px}
.benefit p{font-size:15px;line-height:27px;color:var(--ink);margin-top:44px}

/* contact */
.contact{left:0;top:4526px;width:1200px;height:474px;background:linear-gradient(180deg,#38404c 0%,#2a313b 45%,#1b2028 100%)}
.contact .eyebrow,.contact h2{color:#fff}
.contact h2{font-size:32px}
.point{position:absolute;left:140px;display:flex;align-items:center;gap:24px;color:#fff;font-size:13px;line-height:19px}
.point .ring{width:50px;height:50px;border-radius:50%;border:1.5px solid #fff;display:flex;align-items:center;justify-content:center}
.point .ring svg{width:20px;height:20px}
.form{position:absolute;left:653px;top:68px;width:405px;height:344px;background:#f7f7f7;border-radius:6px 6px 0 0;padding:34px 34px 0}
.form .row{display:flex;gap:10px;margin-bottom:14px}
.field{flex:1;height:33px;background:var(--field);font-size:10px;color:var(--ink);padding:10px 8px}
.field.tall{height:112px}
.form .submit{position:absolute;left:0;bottom:-61px;width:405px;height:61px;background:var(--orange);color:#fff;font-size:14px;font-weight:600;display:flex;align-items:center;justify-content:center}

/* footer */
.foot-brand{left:0;top:5030px;width:1200px;text-align:center}
.foot-brand .name{font-family:"Syncopate",sans-serif;font-weight:700;font-size:40px;color:var(--ink);letter-spacing:2px}
.foot-brand .tag{font-size:17px;font-weight:600;color:var(--teal);letter-spacing:5px;text-transform:uppercase}
.socials{left:0;top:5194px;width:1200px;display:flex;justify-content:center;gap:12px}
.socials span{width:36px;height:36px;border-radius:50%;background:var(--orange)}
.copyright{left:0;top:5268px;width:1200px;height:46px;background:var(--teal);color:#fff;font-size:11px;display:flex;align-items:center;justify-content:center}
</style>
</head>
<body>
<svg width="0" height="0" style="position:absolute">
  <defs>
    <symbol id="bolt" viewBox="0 0 30 52"><polygon points="18,0 2,30 13,30 6,52 28,18 16,18 24,0" fill="#f26a24" stroke="#fff" stroke-width="1.5"/></symbol>
  </defs>
</svg>

<!-- Hero -->
<header class="hero">
  <div class="hero-photo" role="img" aria-label="Photo of a smiling electrician in a cap working at an open breaker panel"></div>
  <div class="topbar-mail">
    <svg width="16" height="12" viewBox="0 0 16 12"><rect x="0.5" y="0.5" width="15" height="11" rx="1" fill="#f26a24"/><path d="M1 1l7 6 7-6" stroke="#fff" fill="none"/></svg>
    support@vantor-wiring.example
  </div>
  <div class="topbar-call">Call Us Now!<br>555-217-4086</div>
  <div class="brand"><div class="name">VANTOR</div><div class="tag">Wiring Service</div></div>
  <h1 class="display">Make us your first<br>choice for<br><span class="accent">Electrical Services</span></h1>
  <p class="lede">Licensed Electricians In Greenville, SC Ensuring Top-tier Service For Every Call.</p>
  <svg class="hero-curves" width="1200" height="640" viewBox="0 0 1200 640">
    <path d="M0,400 C280,520 700,560 1200,430 L1200,640 L0,640 Z" fill="#fff"/>
    <path d="M0,410 C300,520 720,555 1200,425 L1200,470 C800,580 330,570 0,470 Z" fill="#1c6781"/>
    <path d="M0,490 C340,600 820,600 1200,480 L1200,492 C820,620 340,618 0,505 Z" fill="#f26a24"/>
  </svg>
  <div class="cta" style="left:150px;top:345px;width:170px"><svg><use href="#bolt"/></svg>Call Us Now!</div>
</header>

<!-- About -->
<section>
  <div class="abs about-photo" role="img" aria-label="Photo of two electricians in work uniforms carrying cable coils and tool belts"></div>
  <div class="abs about-copy">
    <div class="eyebrow" style="color:var(--orange)">Vantor Wiring Service</div>
    <h2 class="display">About Us</h2>
    <p>At Vantor Wiring, EV Chargers, &amp; Generators, your electrical emergency is our urgency. We have Licensed Electricians in Greenville, SC, Raleigh, NC, and Charlotte, NC, ensuring top-tier service for every call. We've built our reputation as the go-to Emergency Electrician for homeowners in need. When you find yourself thinking about an "electrician near me," think of us. While many electrical contractors chase after large-scale construction and commercial building projects, we prioritize you – the homeowner.</p>
    <p>We're committed to delivering unbeatable same-day service for all your residential electrical repairs, EV chargers &amp; Generator installations. With us, you're not just another job; you're our top priority. Choose Vantor Wiring for swift, safe, &amp; standout electrical solutions.</p>
  </div>
  <div class="cta" style="left:640px;top:1108px;width:170px"><svg><use href="#bolt"/></svg>Call Us Now!</div>
</section>

<!-- Services -->
<section class="abs services">
  <div class="abs center eyebrow" style="top:83px;color:#fff">Our Services</div>
  <h2 class="abs center display" style="top:102px;font-size:31px;color:#fff">What We Do</h2>
  <div class="card" style="left:140px">
    <div class="shot" role="img" aria-label="Photo of a tripped circuit breaker being reset" style="background:linear-gradient(160deg,#5b5f66,#2d3036)"></div>
    <h3>Partial Power Outages</h3>
    <p>Prolonged darkness or interrupted power supply can disrupt your routine. We ensure that your power is restored swiftly.</p>
    <a>LEARN MORE</a>
  </div>
  <div class="card" style="left:375px">
    <div class="shot" role="img" aria-label="Photo of a multimeter testing a wall outlet" style="background:linear-gradient(160deg,#d9d9d6,#8d8f8c)"></div>
    <h3>Outlets Not Working</h3>
    <p>As foundational elements of any residential or commercial property, outlets and switches are easy to overlook—until they stop...</p>
    <a>LEARN MORE</a>
  </div>
  <div class="card" style="left:610px">
    <div class="shot" role="img" aria-label="Photo of an electrician servicing a home electrical panel" style="background:linear-gradient(160deg,#c8ccd0,#4d5a6b)"></div>
    <h3>Electrical Panel Repairs</h3>
    <p>From minor glitches to significant malfunctions, we're adept at diagnosing &amp; resolving all electrical panel issues.</p>
    <a>LEARN MORE</a>
  </div>
  <div class="card" style="left:843px">
    <div class="shot" role="img" aria-label="Photo of an electrician in a hard hat inspecting a fuse box" style="background:linear-gradient(160deg,#e8e8ea,#b33c34 60%,#3e4048)"></div>
    <h3>Fusebox Repairs</h3>
    <p>Protect your electrical system with our expert fuse box repair services. Lorem ipsum dolor sit consectetur adipiscing elit.</p>
    <a>LEARN MORE</a>
  </div>
  <div class="cta light" style="left:520px;top:664px;width:170px"><svg><use href="#bolt"/></svg>Call Us Now!</div>
</section>

<!-- Try -->
<section class="try">
  <h2 class="abs center display" style="top:2068px">Try our services once and you<br>won't need to go anywhere else</h2>
  <div class="abs center" style="top:2163px;font-size:15.5px;color:var(--ink)">Expert Solutions And Excellent Service</div>
  <div class="cta" style="left:520px;top:2205px;width:170px"><svg><use href="#bolt"/></svg>Call Us Now!</div>
</section>

<!-- Reviews -->
<section class="abs reviews">
  <div class="abs center eyebrow" style="top:88px">Testimonials</div>
  <h2 class="abs center display" style="top:104px;font-size:31px">Customer Reviews</h2>
  <div class="abs center" style="top:150px"><div class="rule" style="background:var(--ink)"></div></div>
  <div class="listings">
    <div>Searchly<span class="stars">★★★★★</span></div>
    <div>Rately<span class="stars">★★★★★</span></div>
    <div class="badge" role="img" aria-label="TCB accreditation badge"></div>
    <div>Friendnet<span class="stars">★★★★★</span></div>
  </div>
  <div class="avatar" role="img" aria-label="Reviewer portrait" style="left:327px"></div>
  <div class="review" style="left:140px">
    <span class="src"></span>
    <h4>Maren Holt</h4>
    <div class="stars">★★★★★</div>
    <p>Searched on Searchly for an electrician and Theo from Upstate responded. He was very friendly, professional and showed interest in my dilemma. He made it easy to talk to and helped me understand the urgency of my situation. He not only solved the issue...</p>
  </div>
  <div class="avatar" role="img" aria-label="Reviewer portrait" style="left:801px"></div>
  <div class="review" style="left:615px">
    <span class="src"></span>
    <h4>Leah Dunmore</h4>
    <div class="stars">★★★★★</div>
    <p>Theo was wonderful and immediately identified what was tripping an electrical breaker box out by our pool. He then installed an electrical outlet for me that I requested in the attic; both jobs done very well in about an hours time. Thank you Theo! Will definitely...</p>
  </div>
</section>
<div class="nav-prev">‹</div>
<div class="nav-next">›</div>

<!-- Gallery -->
<section>
  <div class="abs center eyebrow" style="top:2979px;color:var(--orange)">Our Projects</div>
  <h2 class="abs center display" style="top:2996px;font-size:31px">Work Gallery</h2>
  <div class="tile feature" role="img" aria-label="Photo of an electrician working at an outdoor meter box" style="left:140px;top:3080px;width:280px;height:405px;background:linear-gradient(170deg,#8a8f94,#4b5158)">
    <div class="cap"><h5>LOREM IPSUM DOLOR</h5><p>Lorem ipsum dolor sit amet, consectetur adipiscing elit. Vestibulum laoreet ex ac interdum sodales.</p><div class="plus">+</div></div>
  </div>
  <div class="tile" role="img" aria-label="Photo of hands wiring circuit breakers" style="left:430px;top:3080px;width:338px;height:196px;background:linear-gradient(160deg,#cfd2d6,#6a6f78 60%,#b8463a)"></div>
  <div class="tile" role="img" aria-label="Photo of hands installing a wall socket" style="left:430px;top:3288px;width:338px;height:197px;background:linear-gradient(160deg,#f1ece6,#c9b3a2)"></div>
  <div class="tile" role="img" aria-label="Photo of a hand resetting a breaker in a panel" style="left:778px;top:3080px;width:280px;height:405px;background:linear-gradient(170deg,#4a4c52,#c9966f 60%,#6e5142)"></div>
</section>

<!-- Need our services -->
<section class="abs need">
  <h2 class="display">Need Our Services?</h2>
  <p>Vantor Wiring Service Can Be Contacted In a Number of Ways</p>
  <div class="cta" style="left:610px;top:159px;width:147px"><svg><use href="#bolt"/></svg>Call Us Now!</div>
  <div class="cta" style="left:785px;top:159px;width:165px"><svg><use href="#bolt"/></svg>555-217-4086</div>
</section>
<div class="abs need-person" role="img" aria-label="Illustrated electrician in a hard hat and overalls giving a thumbs up"></div>

<!-- Why choose us -->
<section class="why">
  <div class="abs center eyebrow" style="top:4034px;color:var(--orange)">Benefits</div>
  <h2 class="abs center display" style="top:4052px;font-size:31px">Why Choose Us</h2>
  <div class="abs center" style="top:4100px"><div class="rule"></div></div>
  <p class="abs center lead" style="top:4125px">Need to hire a local electrician? Vantor Wiring Service is the company to call.<br>You'll be pleased to know that</p>
  <div class="benefit" style="left:185px">
    <svg viewBox="0 0 70 70" fill="none" stroke="#17171f" stroke-width="2"><circle cx="35" cy="30" r="7"/><path d="M22 56c0-9 6-14 13-14s13 5 13 14"/><path d="M18 16l2 4 4 1-3 3 1 4-4-2-4 2 1-4-3-3 4-1z" stroke="#f26a24"/><path d="M52 16l2 4 4 1-3 3 1 4-4-2-4 2 1-4-3-3 4-1z" stroke="#f26a24"/><path d="M35 4l2 4 4 1-3 3 1 4-4-2-4 2 1-4-3-3 4-1z" stroke="#f26a24"/></svg>
    <p>We Have A Decade<br>of Experience</p>
  </div>
  <div class="benefit" style="left:457px">
    <svg viewBox="0 0 70 70" fill="none" stroke="#17171f" stroke-width="2"><rect x="16" y="8" width="34" height="44" rx="2"/><path d="M22 18h22M22 25h22M22 32h12"/><circle cx="44" cy="44" r="8" stroke="#f26a24"/><path d="M39 51l-3 12 8-4 8 4-3-12" stroke="#f26a24"/></svg>
    <p>Vantor Wiring Service Is<br>Fully Licensed And Insured</p>
  </div>
  <div class="benefit" style="left:747px">
    <svg viewBox="0 0 70 70" fill="none" stroke="#17171f" stroke-width="2"><rect x="12" y="10" width="30" height="48" rx="2"/><path d="M18 20h18M18 28h18M18 36h12"/><rect x="36" y="30" width="22" height="30" rx="2" stroke="#f26a24"/><path d="M40 36h14M40 44h4M48 44h4M40 51h4M48 51h4" stroke="#f26a24"/></svg>
    <p>We Offer Free Estimates</p>
  </div>
  <div class="cta" style="left:520px;top:4405px;width:170px"><svg><use href="#bolt"/></svg>Call Us Now!</div>
</section>

<!-- Contact -->
<section class="abs contact" role="group" aria-label="Get in touch">
  <div role="img" aria-label="Dusk view of the Greenville city skyline" class="abs" style="inset:0;background:linear-gradient(180deg,rgba(120,110,100,.25),rgba(0,0,0,0) 60%)"></div>
  <div class="abs eyebrow" style="left:142px;top:95px;color:#fff">Quick Contact</div>
  <h2 class="abs display" style="left:142px;top:112px">Get In Touch</h2>
  <div class="point" style="top:178px">
    <div class="ring"><svg viewBox="0 0 20 20" fill="#fff"><path d="M10 1a6 6 0 0 0-6 6c0 5 6 12 6 12s6-7 6-12a6 6 0 0 0-6-6zm0 8.5A2.5 2.5 0 1 1 10 4.5a2.5 2.5 0 0 1 0 5z"/></svg></div>
    <div>120 Cedar Ridge Ln Suite 4<br>Greenville, SC 29601</div>
  </div>
  <div class="point" style="top:250px">
    <div class="ring"><svg viewBox="0 0 20 20" fill="#fff"><path d="M4 2l3 0 2 4-2 2c1 2 3 4 5 5l2-2 4 2v3c0 1-1 2-2 2C9 18 2 11 2 4c0-1 1-2 2-2z"/></svg></div>
    <div>Call Us Now!<br>555-217-4086</div>
  </div>
  <div class="point" style="top:323px">
    <div class="ring"><svg viewBox="0 0 20 20" fill="none" stroke="#fff" stroke-width="1.6"><rect x="2" y="4" width="16" height="12" rx="1"/><path d="M2 5l8 6 8-6"/></svg></div>
    <div>Email<br>support@vantor-wiring.example</div>
  </div>
  <div class="form">
    <div class="row"><div class="field">First Name</div><div class="field">Last Name</div></div>
    <div class="row"><div class="field">Email Address</div><div class="field">Phone Number</div></div>
    <div class="row"><div class="field tall">Write Comments</div></div>
    <div class="submit">Submit Now</div>
  </div>
</section>

<!-- Footer -->
<footer>
  <div class="abs foot-brand"><div class="name">VANTOR</div><div class="tag">Wiring Service</div></div>
  <div class="abs socials">
    <span role="img" aria-label="Friendnet"></span>
    <span role="img" aria-label="Chirpline"></span>
    <span role="img" aria-label="Workwire"></span>
  </div>
  <div class="abs copyright">Copyright © 2023 VANTOR WIRING SERVICE. All Rights Reserved.</div>
</footer>
</body>
</html>
```